Stationery Design

Need a stationery design for an established accounting firm based in London, England.

The company’s name is ‘Marcus Thorne’. We provide a broad range of bookkeeping, accounting, audit, tax and business services to a wide range of clients (ie, individuals, company, partnerships, etc).

The stationary design needs to show strength and trust and should be clean, corporate and professional.

Only 2 colours must be used as noted on the logo.

The fonts are in Optima

We need the following:

#1: Business Cards (design on 2 sides)
#2: Letterhead (word format) and can be sent to printers
#3: Continuation sheets (word format) and can be sent to printers
#4: Sales invoice template (word format) and can be sent to printers
#5: Report Cover front and back for binding,
#6: Complimentary Slips,
#7: Legal corners with our logo only
#7: Email signature templates

I have attached my company's logo in various file formats

We also need to have our accountancy association’s logo and this must be in the same colour as the dark blue. This IFRB logo must be at least 8mm square (can be larger). I have attached the IFRB logo in various file formats

I have also attached other information that you will need for the letter head and invoice templates

I have also attached our old letterhead, fee note template for reference
Updates

Dear Designers - I have increased the budget

Dear Designers - I have read your comments on the fact that the prize does not reflect the work. Thank you and I appreciate your comments. Unfortunately, I am a start up and my budget is limited. As an Alternative, I have reduced the work that I am asking for to the following items and I hope you can assist: #1: Business Cards (design on 2 sides) #2: Letterhead (word format) and can be sent to printers #3: Report Cover front and back for binding, #4: Email signature templates Regards

Industry/Entity Type

Accounting

```html
<!DOCTYPE html>
<html lang="en">
<head>
<meta charset="utf-8">
<title>Marcus Thorne Accountants – Business Cards</title>
<link rel="stylesheet" href="https://fonts.googleapis.com/css2?family=PT+Sans:wght@400;700&display=swap">
<style>
  :root {
    --backdrop: #b7c9d9;
    --navy: #1a4670;
    --purple: #8e3391;
    --paper: #ffffff;
    --grey-text: #7d8289;
    --rule: #9aa0a6;
  }
  * { margin: 0; padding: 0; box-sizing: border-box; }
  html, body { width: 1200px; height: 1000px; overflow: hidden; }
  body {
    background: var(--backdrop);
    font-family: "PT Sans", sans-serif;
    position: relative;
  }
  .card {
    position: absolute;
    width: 500px;
    height: 310px;
    box-shadow: 0 6px 14px rgba(30, 50, 70, 0.25);
  }
  .card--front {
    left: 120px;
    top: 140px;
    background: var(--navy);
    display: flex;
    align-items: center;
    justify-content: center;
    gap: 12px;
  }
  .front-name {
    color: var(--paper);
    font-size: 30px;
    letter-spacing: 0.04em;
  }
  .front-square {
    width: 22px; height: 22px;
    background: var(--purple);
  }
  .card--back {
    left: 580px;
    top: 520px;
    background: var(--paper);
    color: var(--navy);
  }
  .brand {
    position: absolute;
    left: 28px; top: 150px;
    display: flex; align-items: center; gap: 8px;
  }
  .brand-square { width: 16px; height: 16px; background: var(--purple); }
  .brand-text { line-height: 1; }
  .brand-name { font-size: 19px; letter-spacing: 0.02em; }
  .brand-tag { font-size: 7px; letter-spacing: 0.2em; text-align: right; margin-top: 2px; }
  .holder {
    position: absolute;
    right: 28px; top: 60px;
    text-align: right;
    border-bottom: 1px solid var(--rule);
    padding-bottom: 3px;
    min-width: 110px;
  }
  .holder-name { font-size: 21px; line-height: 1.1; }
  .holder-role { font-size: 17px; line-height: 1.1; color: var(--purple); }
  .divider {
    position: absolute;
    left: 28px; right: 28px; top: 200px;
    border-top: 1px solid var(--rule);
  }
  .contact {
    position: absolute;
    right: 28px; top: 116px;
    font-size: 10.5px;
    line-height: 1.5;
    color: var(--grey-text);
    list-style: none;
  }
  .address {
    position: absolute;
    left: 28px; bottom: 22px;
    font-size: 10.5px;
    line-height: 1.5;
    color: var(--grey-text);
    font-style: normal;
  }
</style>
</head>
<body>
  <section class="card card--front" aria-label="Business card front">
    <span class="front-square" aria-hidden="true"></span>
    <span class="front-name">MARCUS THORNE</span>
  </section>

  <section class="card card--back" aria-label="Business card back">
    <div class="brand">
      <span class="brand-square" aria-hidden="true"></span>
      <div class="brand-text">
        <div class="brand-name">MARCUS THORNE</div>
        <div class="brand-tag">ACCOUNTANTS</div>
      </div>
    </div>
    <div class="holder">
      <div class="holder-name">Daniel Hart</div>
      <div class="holder-role">Director</div>
    </div>
    <ul class="contact">
      <li>T: 020 7946 0321</li>
      <li>F: 020 7946 0322</li>
      <li>E: mail@marcusthorne.co.uk</li>
      <li>W: www.marcusthorne.co.uk</li>
    </ul>
    <div class="divider"></div>
    <address class="address">
      12 Calder Court,<br>
      Linfield Business Park,<br>
      Ashworth Road, Ashcombe-on-the-Vale,<br>
      Westmere AV4 7QR
    </address>
  </section>
</body>
</html>
```